VENTURE CAPITAL GROUP BUSINESS CARD DESIGN

Venture Capital Group based in SF looking for a bold business card design. No trendy colour explosion, 3D effects etc. Just "simple" optical effects. Works on your brain, keeps your eye focused and sticks to your mind.
Target Market(s)
Technology startups
Industry/Entity Type
Venture Capital
Contact Information for Business Card
DESMOND WHITLAKE
MANAGING PARTNER
187 FENWORTH ST SAN FRANCISCO, CA 94187
415.555.0142 O
415.555.0147 F
415.555.0193 C
desmond@veldtmoorcapital.ventures

```html
<!DOCTYPE html>
<html lang="en">
<head>
<meta charset="utf-8">
<title>Veldtmoor Capital Group – Business Card</title>
<link rel="stylesheet" href="https://fonts.googleapis.com/css2?family=PT+Sans:wght@400;700&display=swap">
<style>
  :root {
    --bg: #e9e7e3;
    --card-white: #ffffff;
    --green: #2f8a2f;
    --green-dark: #1f6b22;
    --green-light: #58b24c;
    --grey: #8c8c8e;
    --grey-dark: #5e5e60;
    --grey-light: #c9c9cb;
    --ink: #4a4a4c;
    --shadow: rgba(0,0,0,0.18);
  }
  * { margin: 0; padding: 0; box-sizing: border-box; }
  html, body { width: 1200px; height: 950px; overflow: hidden; }
  body {
    background: var(--bg);
    font-family: "PT Sans", sans-serif;
    position: relative;
  }
  .card {
    position: absolute;
    width: 540px;
    height: 310px;
    border-radius: 18px;
    overflow: hidden;
    box-shadow: 0 6px 18px var(--shadow);
    top: 320px;
  }
  .card-front { left: 40px; background: var(--card-white); }
  .card-back {
    left: 620px;
    background: radial-gradient(ellipse at 55% 45%, #b4b4b6 0%, var(--grey) 55%, var(--grey-dark) 100%);
  }
  .front-swoosh { position: absolute; inset: 0; }
  .holder {
    position: absolute;
    right: 120px;
    top: 34px;
    text-align: right;
  }
  .holder-name {
    font-weight: 700;
    font-size: 22px;
    color: var(--green);
    letter-spacing: 0.3px;
  }
  .holder-title {
    font-size: 14px;
    color: var(--grey);
    margin-top: 2px;
  }
  .brand {
    position: absolute;
    left: 32px;
    top: 112px;
    display: flex;
    align-items: center;
    gap: 10px;
  }
  .brand-dot {
    width: 22px; height: 22px;
    border-radius: 50%;
    background: var(--green);
  }
  .brand-name {
    font-size: 26px;
    color: var(--green);
    letter-spacing: 2px;
  }
  .contact {
    position: absolute;
    left: 32px;
    top: 168px;
    font-size: 13px;
    color: var(--ink);
    line-height: 18px;
  }
  .contact-line { display: flex; align-items: center; gap: 7px; }
  .contact-line svg { width: 12px; height: 12px; flex: none; }
  .address { margin-bottom: 4px; }
  .back-mark {
    position: absolute;
    left: 50%; top: 50%;
    transform: translate(-50%, -50%);
    width: 170px; height: 170px;
    border-radius: 50%;
    background: radial-gradient(circle at 45% 40%, #ffffff 0%, #e6e6e6 70%, #cfcfd1 100%);
    display: flex; align-items: center; justify-content: center;
  }
  .back-mark .brand-name { font-size: 24px; }
  .website {
    position: absolute;
    left: 26px;
    top: 50%;
    transform: translateY(-50%) rotate(180deg);
    writing-mode: vertical-rl;
    font-size: 14px;
    color: #f2f2f2;
    letter-spacing: 0.6px;
  }
</style>
</head>
<body>
  <section class="card card-front">
    <svg class="front-swoosh" viewBox="0 0 540 310" aria-hidden="true">
      <defs>
        <linearGradient id="band-grey" x1="0" y1="0" x2="1" y2="1">
          <stop offset="0" stop-color="#f0f0f1"/>
          <stop offset="0.5" stop-color="#a6a6a8"/>
          <stop offset="1" stop-color="#6e6e70"/>
        </linearGradient>
        <linearGradient id="band-green" x1="0" y1="0" x2="1" y2="1">
          <stop offset="0" stop-color="#58b24c"/>
          <stop offset="1" stop-color="#1f6b22"/>
        </linearGradient>
      </defs>
      <path d="M330 0 C450 40 510 150 515 310 H540 V0 Z" fill="url(#band-grey)"/>
      <path d="M400 0 C490 40 535 120 540 220 V0 Z" fill="url(#band-green)"/>
    </svg>

    <div class="holder">
      <div class="holder-name">DESMOND WHITLAKE</div>
      <div class="holder-title">Managing Partner</div>
    </div>

    <div class="brand">
      <span class="brand-name">VELDTMOOR</span>
    </div>

    <div class="contact">
      <div class="address">187 FENWORTH ST<br>San Francisco, CA 94187</div>
      <div class="contact-line">
        <svg viewBox="0 0 12 12"><path d="M2 1 L4.5 1 L5.5 3.5 L4 4.5 C4.8 6.3 5.7 7.2 7.5 8 L8.5 6.5 L11 7.5 L11 10 C6 10.5 1.5 6 2 1 Z" fill="var(--ink)"/></svg>
        <span>415.555.0142</span>
      </div>
      <div class="contact-line">
        <svg viewBox="0 0 12 12"><rect x="1.5" y="1.5" width="9" height="9" fill="none" stroke="var(--ink)" stroke-width="1.3"/></svg>
        <span>415.555.0147</span>
      </div>
      <div class="contact-line">
        <svg viewBox="0 0 12 12"><rect x="3" y="0.8" width="6" height="10.4" rx="1" fill="var(--ink)"/><rect x="4" y="2" width="4" height="6" fill="#fff"/></svg>
        <span>415.555.0193</span>
      </div>
      <div class="contact-line">
        <svg viewBox="0 0 12 12"><rect x="1" y="2.5" width="10" height="7" fill="var(--ink)"/><path d="M1 2.5 L6 6.5 L11 2.5" fill="none" stroke="#fff" stroke-width="1"/></svg>
        <span>desmond@veldtmoorcapital.ventures</span>
      </div>
    </div>
  </section>

  <section class="card card-back">
    <div class="website">www.veldtmoorcapital.ventures</div>
    <div class="back-mark">
      <span class="brand-name">VELDTMOOR</span>
    </div>
  </section>
</body>
</html>
```